Design my site www.brieflyledger.com

So here is what I am thinking in terms of design:

https://plenvo.com

https://www.skyluxair.com

http://kalvex.com/harbor-plaza-tower/

I want the theme to be white and blue (royal blue). I attached a paint picture of what I would like the site to look like in terms of placing the text. Generally, what I like about the sites above is that they are simple, you can navigate easily and have some kind of idea of what's going on by looking at the center (picture and motto). Let's establish a clear understanding of how the functional part of the site would look like. Please see the picture attached.

I want to keep it simple: On top would be the Name 'BRIEFLY ledger", somewhere to the right on top on the page would be 'Sign in" button.

In the center would be a picture (maybe a video) with the Motto (on top of it all in capital) OBSERVE NAVIGATE DECIDE and below would be the "sign up now"

Below the picture (like on kalvex.com site) or to the left on top of the page would be "About Us', "Press" "Contact Us' buttons.

Then once the user gets to his page his got 3 tabs " Press Headlines", "Events", " Briefings".

we would keep the same format I only have on the site, but separate for every Tab.

I do not want the user to get distracted. I also want him to be able to access the page though mobile phone and be able to get automatic updates just like Zorvan Pings without having to sign in daily.

The landing page must be minimalist yet with business/corporate feel where users can navigate easily and a "what you see is what you get" approach. You want an image or video (personally I prefer the video.. it does capture the users attention instantly, as long as it is an interesting video), with your taglines in it.

Sections available to public: About Us, Contact Us, Landing Page with Signup Option

Private: Public Sections + User Account Page, Tabs for (Events, Press Headlines, Briefings)

Target Market(s)

PR/media monitoring/diplomatic community

Coding

Coded - Design and coding required

Number of Pages Required

1 page

Font styles to use
Serif
Sans Serif

Colors
0255a3
ec1f27

Requirements
Must have
• a simple landing page, that is user friendly.
Nice to have
• a video with the explanation of how to navigate the site
Should not have
• too many colors, graphs etc.

```html
<!DOCTYPE html>
<html lang="en">
<head>
<meta charset="utf-8">
<title>Briefly Ledger – Events</title>
<link href="https://fonts.googleapis.com/css2?family=Open+Sans:wght@400;600&family=Montserrat:wght@600&display=swap" rel="stylesheet">
<style>
:root{
  --blue:#2b8fc0;
  --blue-dark:#1f79a6;
  --text:#444;
  --label:#555;
  --panel:#f5f5f5;
  --line:#dcdcdc;
  --footer:#f7f7f7;
  --white:#fff;
}
*{box-sizing:border-box;margin:0;padding:0}
html,body{width:1200px;height:896px;overflow:hidden;background:var(--white);font-family:"Open Sans",Arial,sans-serif;color:var(--text)}
.page{position:relative;width:1200px;height:896px}
.hero{position:absolute;left:0;top:0;width:1200px;height:257px;
  background:linear-gradient(180deg,#4a5563 0%,#3a4552 35%,#2b3138 70%,#1f2327 100%)}
.hero-photo{position:absolute;inset:0}
.brand{position:absolute;left:99px;top:39px;width:321px;height:57px;border:2px solid var(--white);
  display:flex;align-items:center;justify-content:center;
  font-family:"Montserrat",Arial,sans-serif;font-weight:600;font-size:30px;color:var(--white);letter-spacing:-.5px}
.sign-in{position:absolute;left:982px;top:51px;width:83px;height:33px;border-radius:3px;border:1px solid #7cc3e6;
  background:var(--blue);color:var(--white);font-family:"Montserrat",Arial,sans-serif;font-weight:600;font-size:13px;
  display:flex;align-items:center;justify-content:center}
.menu-icon{position:absolute;left:1078px;top:58px}
.tabs{position:absolute;left:98px;top:296px;width:1003px;height:43px;border-bottom:1px solid var(--blue)}
.tab{position:absolute;top:0;height:42px;display:flex;align-items:center;justify-content:center;
  font-size:15.5px;font-weight:600;color:#444;text-transform:uppercase}
.tab-press{left:0;width:213px}
.tab-events{left:213px;width:207px;background:var(--blue);color:var(--white)}
.tab-briefings{left:420px;width:211px}
.panel{position:absolute;left:98px;top:338px;width:1003px;height:381px;background:var(--panel);
  border:1px solid #e2e2e2;border-top:none}
.field{position:absolute;width:348px}
.field label{display:block;font-size:13.5px;color:var(--label);height:18px}
.input{margin-top:0;position:absolute;top:18px;width:348px;height:35px;background:var(--white);border:1px solid var(--line);border-radius:2px}
.input::after{content:"";position:absolute;right:34px;top:0;bottom:0;border-left:1px solid #eee}
.select{display:flex;align-items:center;padding-left:11px;font-size:11px;color:#666}
.select::after{border-left-color:var(--line)}
.caret{position:absolute;right:12px;top:15px}
.submit{position:absolute;left:50px;top:276px;width:128px;height:37px;background:var(--blue);color:var(--white);
  border-radius:2px;display:flex;align-items:center;justify-content:center;font-size:15.5px}
.footer{position:absolute;left:0;top:785px;width:1200px;height:111px;background:var(--footer);border-top:1px solid #ececec}
.footer-nav{position:absolute;left:99px;top:37px;font-size:12.5px;color:var(--blue)}
.footer-nav span.sep{color:#333;margin:0 10px}
.copyright{position:absolute;left:98px;top:64px;font-size:12.5px;color:#333}
.social{position:absolute;left:927px;top:35px;display:flex;gap:8px}
.social i{display:block;width:28px;height:28px;border-radius:50%;background:var(--blue-dark)}
</style>
</head>
<body>
<div class="page">
  <header class="hero">
    <div class="hero-photo" role="img" aria-label="Aerial photograph of a city skyline at dusk"></div>
    <div class="brand">BRIEFLY LEDGER</div>
    <div class="sign-in">SIGN IN</div>
    <svg class="menu-icon" width="22" height="20" viewBox="0 0 22 20" aria-label="Menu">
      <rect x="0" y="0" width="22" height="3.5" fill="#fff"/>
      <rect x="0" y="8" width="22" height="3.5" fill="#fff"/>
      <rect x="0" y="16" width="22" height="3.5" fill="#fff"/>
    </svg>
  </header>

  <nav class="tabs">
    <div class="tab tab-press">Press Headlines</div>
    <div class="tab tab-events">Events</div>
    <div class="tab tab-briefings">Briefings</div>
  </nav>

  <section class="panel">
    <div class="field" style="left:48px;top:56px"><label>Event Name :</label><div class="input"></div></div>
    <div class="field" style="left:425px;top:56px"><label>Status :</label><div class="input"></div></div>
    <div class="field" style="left:48px;top:125px"><label>Event Type :</label><div class="input"></div></div>
    <div class="field" style="left:425px;top:125px"><label>Address :</label><div class="input"></div></div>
    <div class="field" style="left:48px;top:194px"><label>Event Date range :</label>
      <div class="input select">Past 24 hours
        <svg class="caret" width="9" height="5" viewBox="0 0 9 5"><path d="M0 0h9L4.5 5z" fill="#555"/></svg></div></div>
    <div class="field" style="left:425px;top:194px"><label>Country :</label>
      <div class="input select">All
        <svg class="caret" width="9" height="5" viewBox="0 0 9 5"><path d="M0 0h9L4.5 5z" fill="#555"/></svg></div></div>
    <div class="submit">SUBMIT</div>
  </section>

  <footer class="footer">
    <div class="footer-nav">ABOUT US<span class="sep">/</span>PRESS<span class="sep">/</span>CONTACT US</div>
    <div class="copyright">2016 © Copyrights BRIEFLY ledger.All Rights Reserved</div>
    <div class="social" aria-label="Social links"><i></i><i></i><i></i><i></i><i></i></div>
  </footer>
</div>
</body>
</html>
```